Upscale business cards needed for Board of Directors

We need professional business cards created for members of our family business Board of Directors. We would like these relatively simple and straightforward, but also with a unique element to set them apart. Probably stick with neutral and simple colors - white, grey etc. We need space for the traditional elements, including name, title, address, email/phone number. And we will be creating several from this template so it needs to be template that is easy to switch information in and out of.
Business
See description

```html
<!DOCTYPE html>
<html lang="en">
<head>
<meta charset="utf-8">
<title>Corvane Holdings — Business Card</title>
<link href="https://fonts.googleapis.com/css2?family=Open+Sans:wght@400;600&display=swap" rel="stylesheet">
<style>
  :root {
    --backdrop: #3a3533;
    --card-black: #0f0f0f;
    --card-gold: #b49f72;
    --accent-gold: #b99b5e;
    --text-light: #f2f2f2;
    --text-dark: #1a1a1a;
  }
  * { margin: 0; padding: 0; box-sizing: border-box; }
  html, body {
    width: 1200px; height: 900px; overflow: hidden;
    background: var(--backdrop);
    font-family: "Open Sans", sans-serif;
  }
  .stage {
    position: relative; width: 1200px; height: 900px;
    display: flex; align-items: center; justify-content: center; gap: 50px;
  }
  .card {
    position: relative; width: 525px; height: 300px;
    box-shadow: 0 10px 30px rgba(0,0,0,.45);
  }
  .card--front { background: var(--card-black); color: var(--text-light); }
  .card--back { background: var(--card-gold); display: flex; align-items: center; justify-content: center; }

  .contact-list {
    position: absolute; top: 28px; right: 28px;
    list-style: none; text-align: right; font-size: 13px; line-height: 22px;
  }
  .contact-list li { display: flex; align-items: center; justify-content: flex-end; gap: 8px; }
  .contact-list svg { width: 11px; height: 11px; fill: var(--accent-gold); }

  .holder { position: absolute; left: 30px; top: 120px; }
  .holder__name { color: var(--accent-gold); font-weight: 600; font-size: 18px; line-height: 22px; }
  .holder__title { font-size: 13px; line-height: 17px; }
  .holder__address { margin-top: 14px; font-size: 13px; line-height: 17px; }

  .company-name {
    font-weight: 600; font-size: 28px; line-height: 1;
    white-space: nowrap;
  }
  .card--front .company-name { position: absolute; right: 30px; bottom: 40px; color: var(--text-light); }
  .card--back .company-name { color: var(--text-dark); }
</style>
</head>
<body>
<main class="stage">
  <section class="card card--front" aria-label="Card front">
    <ul class="contact-list">
      <li>(044)-555-0142
        <svg viewBox="0 0 24 24" aria-hidden="true"><path d="M6.6 10.8a15.1 15.1 0 0 0 6.6 6.6l2.2-2.2c.3-.3.7-.4 1-.2 1.1.4 2.3.6 3.6.6.6 0 1 .4 1 1V20c0 .6-.4 1-1 1A17 17 0 0 1 3 4c0-.6.4-1 1-1h3.5c.6 0 1 .4 1 1 0 1.3.2 2.5.6 3.6.1.3 0 .7-.2 1z"/></svg>
      </li>
      <li>info@corvane.com
        <svg viewBox="0 0 24 24" aria-hidden="true"><path d="M2 5h20v14H2z M3 6l9 7 9-7" fill="none" stroke="#b99b5e" stroke-width="2"/></svg>
      </li>
      <li>www.corvane.com
        <svg viewBox="0 0 24 24" aria-hidden="true"><circle cx="12" cy="12" r="11"/></svg>
      </li>
    </ul>
    <div class="holder">
      <p class="holder__name">Daniel Whitford</p>
      <p class="holder__title">Managing Director</p>
      <p class="holder__address">48 Quayside Lane, Suite 12<br>Northport, 204816</p>
    </div>
    <p class="company-name">Corvane Holdings</p>
  </section>

  <section class="card card--back" aria-label="Card back">
    <p class="company-name">Corvane Holdings</p>
  </section>
</main>
</body>
</html>
```